Kor'v Meridell Travel

We need a sleek, professional, inviting card to elicit global travel for the experienced and professional traveler. Royal blue, black and silver. (perhaps the wording could be silver with black shadow?-get creative) Maybe a watermark on the front and the full raised logo on the back.
We want a stylish and modern card, but professional.

```html
<!DOCTYPE html>
<html lang="en">
<head>
<meta charset="utf-8">
<title>Kor'v Meridell Travel — Business Card</title>
<link rel="stylesheet" href="https://fonts.googleapis.com/css2?family=League+Spartan:wght@600&family=Arimo:wght@400&display=swap">
<style>
  :root {
    --backdrop: #a3a3a3;
    --brand-green: #8dc63f;
    --brand-blue: #27a9e1;
    --paper: #ffffff;
    --ink: #1d1d1d;
    --rule: #9a9a9a;
  }
  * { margin: 0; padding: 0; box-sizing: border-box; }
  html, body { width: 1200px; height: 1200px; overflow: hidden; }
  body { background: var(--backdrop); position: relative; font-family: "Arimo", Arial, sans-serif; }

  .card { position: absolute; top: 303px; width: 369px; height: 594px; }

  .card-front {
    left: 201px;
    background: linear-gradient(180deg, var(--brand-green) 0%, #5cbf8a 40%, #3cb2c0 65%, var(--brand-blue) 100%);
  }
  .front-name {
    position: absolute; left: 0; right: 0; top: 488px;
    text-align: center; color: #fff;
    font-family: "League Spartan", "Montserrat", sans-serif; font-weight: 600;
    font-size: 33px; line-height: 1; letter-spacing: 0.5px;
  }
  .front-name span { display: block; letter-spacing: 6px; font-size: 22px; margin-top: 4px; }

  .card-back { left: 599px; background: var(--paper); text-align: center; }

  .brand { position: absolute; left: 0; right: 0; top: 92px; display: flex; flex-direction: column; align-items: center; }
  .brand-mark { width: 50px; height: 50px; border-radius: 50%; background: var(--brand-blue); margin-bottom: 22px; }
  .brand-name {
    font-family: "League Spartan", "Montserrat", sans-serif; font-weight: 600;
    color: var(--brand-blue); font-size: 31px; line-height: 1; letter-spacing: 0.5px;
  }
  .brand-name span { display: block; font-size: 21px; letter-spacing: 6px; margin-top: 4px; }

  .person { position: absolute; left: 0; right: 0; top: 306px; }
  .person-name {
    font-family: "League Spartan", "Montserrat", sans-serif; font-weight: 600;
    color: var(--brand-blue); font-size: 23px; letter-spacing: 0.3px;
  }
  .person-title { color: var(--brand-green); font-size: 15px; margin-top: 1px; letter-spacing: 0.3px; }

  .contact-icons {
    position: absolute; left: 87px; width: 190px; top: 364px;
    display: flex; align-items: center; justify-content: center; gap: 4px;
  }
  .contact-icons .line { flex: 1; height: 1px; background: var(--rule); }
  .contact-icons .line:first-child { margin-right: 4px; }
  .contact-icons .line:last-child { margin-left: 4px; }
  .icon { width: 25px; height: 25px; border-radius: 3px; background: var(--brand-blue); display: flex; align-items: center; justify-content: center; }
  .icon svg { width: 15px; height: 15px; }

  .contact-list { position: absolute; left: 0; right: 0; top: 401px; list-style: none; color: var(--ink); font-size: 16.5px; line-height: 21.7px; }
  .contact-list .accent { color: var(--brand-blue); }

  .divider { position: absolute; left: 89px; width: 194px; top: 497px; height: 1px; background: var(--rule); }

  .address { position: absolute; left: 0; right: 0; top: 511px; color: var(--ink); font-size: 16.5px; line-height: 21.7px; font-style: normal; }
</style>
</head>
<body>
  <section class="card card-front" aria-label="Card front">
    <h1 class="front-name">KOR'V MERIDELL<span>TRAVEL</span></h1>
  </section>

  <section class="card card-back" aria-label="Card back">
    <div class="brand">
      <div class="brand-mark"></div>
      <p class="brand-name">KOR'V MERIDELL<span>TRAVEL</span></p>
    </div>

    <div class="person">
      <h2 class="person-name">ADRIAN VOLLMER</h2>
      <p class="person-title">MANAGING DIRECTOR</p>
    </div>

    <div class="contact-icons">
      <span class="line"></span>
      <span class="icon"><svg viewBox="0 0 16 16" fill="none" stroke="#fff" stroke-width="1.4"><path d="M2 6c0-2 3-3 6-3s6 1 6 3l-2 1-1-2H5L4 7z" fill="#fff"/><rect x="4" y="8" width="8" height="5" rx="1"/></svg></span>
      <span class="icon"><svg viewBox="0 0 16 16" fill="none" stroke="#fff" stroke-width="1.4"><rect x="4.5" y="1.5" width="7" height="13" rx="1.2"/><line x1="7" y1="12.3" x2="9" y2="12.3"/></svg></span>
      <span class="icon"><svg viewBox="0 0 16 16" fill="none" stroke="#fff" stroke-width="1.3"><rect x="1.5" y="3.5" width="13" height="9"/><path d="M1.5 3.5 8 9l6.5-5.5M1.5 12.5l5-4.5M14.5 12.5l-5-4.5"/></svg></span>
      <span class="icon"><svg viewBox="0 0 16 16" fill="none" stroke="#fff" stroke-width="1.3"><circle cx="8" cy="8" r="6.3"/><ellipse cx="8" cy="8" rx="2.8" ry="6.3"/><line x1="1.7" y1="8" x2="14.3" y2="8"/></svg></span>
      <span class="line"></span>
    </div>

    <ul class="contact-list">
      <li>071-318 920 465</li>
      <li>071-318 920 465</li>
      <li>info@korvmeridell.com</li>
      <li>www.<span class="accent">korvmeridell</span>.com</li>
    </ul>

    <div class="divider"></div>

    <address class="address">17 Calder Row, Suite 5<br>60318, Eastmoor Vale</address>
  </section>
</body>
</html>
```